School Poster and Prompt Design

I would like posters created for each of our school values (from the attached Way of Working document). In these posters I would like our logo, and some graphics or pictures - you can use the strategic plan attached for some examples.

I would also like a Code of Conduct Prompt for teachers and students (smaller design that can be used as a sticker for a laptop) based on the attached Tallowmere Heights Basics document. I have also attached a photo example, which we quite like that can be used for a base. This document is called example classroom management prompts.

Target Market(s)

School and students

Requirements
Must have
• Logo built into the design
Our school motto at the bottom 'Strive to Accomplish'
Design that incorporates elements that relate to each of the values.
Design that looks and feels like the example. In our school colours.
Nice to have
• Posters - Easy to read and understand from a distance.
Prompt - Easy to read and understand if turned into a sticker for a laptop.

```html
<!DOCTYPE html>
<html lang="en">
<head>
<meta charset="utf-8">
<title>Tallowmere Heights Basics – Teacher Focus</title>
<link rel="stylesheet" href="https://fonts.googleapis.com/css2?family=Roboto:wght@300;400;500;700;900&display=swap">
<style>
  :root {
    --navy: #14174a;
    --royal: #0c4f8f;
    --mid: #1e87c8;
    --sky: #29bbef;
    --cyan: #29abe2;
    --link: #1e6fb5;
    --ink: #111827;
    --white: #ffffff;
    --backdrop: #e6e7e9;
  }
  * { box-sizing: border-box; margin: 0; padding: 0; }
  html, body { width: 1019px; height: 1200px; overflow: hidden; background: var(--backdrop); }
  body { font-family: "Roboto", Arial, sans-serif; color: var(--ink); position: relative; }
  .poster {
    position: absolute; left: 88px; top: 5px; width: 842px; height: 1190px;
    background: var(--white); overflow: hidden;
  }
  .abs { position: absolute; }
  .header-band {
    left: 0; top: 22px; width: 842px; height: 153px;
    background: linear-gradient(90deg, #1a5b9a 0%, #15296a 45%, var(--navy) 100%);
  }
  .brand-mark { left: 62px; top: 30px; width: 116px; height: 116px; border-radius: 50%; background: #c9d0e8; border: 6px solid var(--white); }
  .brand-name { left: 20px; top: 182px; width: 200px; text-align: center; font-size: 15px; font-weight: 500; color: var(--royal); letter-spacing: .5px; }
  .title { left: 200px; top: 67px; width: 590px; text-align: center; color: var(--white); font-weight: 300; font-size: 31px; line-height: 36px; letter-spacing: 1px; white-space: nowrap; }
  .subtitle { left: 200px; top: 107px; width: 590px; text-align: center; color: var(--cyan); font-weight: 300; font-size: 30px; line-height: 34px; letter-spacing: 1px; white-space: nowrap; }
  .motto { left: 240px; top: 182px; width: 360px; text-align: center; color: var(--link); font-size: 19px; font-weight: 400; letter-spacing: .5px; }

  .entry { left: 27px; top: 229px; width: 788px; height: 215px; background: var(--mid); border-radius: 4px; }
  .entry-notch { left: 397px; top: 229px; }
  .section-title { text-align: center; font-weight: 900; letter-spacing: 1px; }
  .entry .section-title { position: absolute; top: 16px; width: 100%; font-size: 50px; color: var(--white); }
  .card { top: 79px; width: 231px; height: 122px; padding: 18px 20px 0 34px; color: var(--white); font-size: 13px; line-height: 18px; border-radius: 2px; }
  .card--light { background: var(--sky); }
  .card--dark { background: var(--royal); padding-left: 42px; }
  .card h3 { font-size: 16px; font-weight: 700; letter-spacing: 1px; line-height: 19px; margin-bottom: 2px; }
  .card ul { list-style: none; }
  .card li::before { content: "•"; margin-right: 10px; }

  .lesson { left: 22px; top: 467px; width: 798px; height: 208px; }
  .lesson .section-title { position: absolute; top: 20px; width: 100%; font-size: 44px; color: var(--royal); }
  .col { top: 82px; font-size: 13px; line-height: 18.5px; }
  .col h3 { font-size: 16px; font-weight: 500; color: var(--royal); letter-spacing: .5px; margin-bottom: 10px; }
  .col ul { list-style: none; }
  .col li { padding-left: 15px; text-indent: -15px; }
  .col li::before { content: "•"; margin-right: 9px; }

  .exit { left: 0; top: 693px; width: 842px; height: 204px; background: var(--royal); }
  .exit-notch { left: 397px; top: 896px; }
  .exit .section-title { position: absolute; top: 12px; width: 100%; font-size: 46px; color: var(--white); }
  .exit-lead { position: absolute; top: 64px; width: 100%; text-align: center; color: var(--cyan); font-size: 18px; line-height: 21px; letter-spacing: .3px; }
  .check { top: 126px; width: 280px; text-align: center; color: var(--white); font-size: 14px; }
  .check svg { display: block; margin: 0 auto 10px; }

  .recognise-title { left: 0; top: 926px; width: 842px; text-align: center; color: var(--royal); font-size: 19px; font-weight: 400; letter-spacing: .3px; }
  .reward, .habit { width: 280px; text-align: center; color: var(--link); font-size: 14px; line-height: 15px; }
  .reward { top: 960px; }
  .reward svg, .habit svg { display: block; margin: 0 auto 6px; }
  .ensure-band {
    left: 2px; top: 1042px; width: 840px; height: 43px; line-height: 43px; text-align: center;
    background: linear-gradient(90deg, var(--sky) 0%, #1e7bbf 45%, var(--royal) 100%);
    color: var(--white); font-size: 19px; font-weight: 400; letter-spacing: .3px;
  }
  .habit { top: 1094px; }
</style>
</head>
<body>
<main class="poster">
  <div class="abs header-band"></div>
  <div class="abs brand-mark" aria-hidden="true"></div>
  <div class="abs brand-name">TALLOWMERE HEIGHTS</div>
  <h1 class="abs title">TALLOWMERE HEIGHTS BASICS</h1>
  <h2 class="abs subtitle">TEACHER FOCUS</h2>
  <p class="abs motto">STRIVE TO ACCOMPLISH</p>

  <section class="abs entry">
    <h2 class="section-title">ENTRY</h2>
    <div class="abs card card--light" style="left:21px">
      <h3>COMMITMENT</h3>
      <ul><li>On time</li><li>Dressed professionally</li><li>Ready to teach</li></ul>
    </div>
    <div class="abs card card--dark" style="left:278px">
      <h3>COURTESY</h3>
      <ul><li>Greet students warmly</li><li>Notify the office of room changes and leave a note on the door</li></ul>
    </div>
    <div class="abs card card--light" style="left:534px">
      <h3>COOPERATION<br>STUDENTS ARE:</h3>
      <ul><li>In the right seat</li><li>Have the right materials</li><li>Actively listening</li></ul>
    </div>
  </section>
  <svg class="abs entry-notch" width="48" height="14" viewBox="0 0 48 14" aria-hidden="true"><polygon points="0,0 48,0 24,14" fill="#ffffff"/></svg>

  <section class="abs lesson">
    <svg class="abs" width="798" height="208" viewBox="0 0 798 208" aria-hidden="true" style="left:0;top:0">
      <defs>
        <pattern id="chevH" width="7" height="8" patternUnits="userSpaceOnUse"><polyline points="1,1 5,4 1,7" fill="none" stroke="#1e87c8" stroke-width="1.3"/></pattern>
        <pattern id="chevV" width="8" height="7" patternUnits="userSpaceOnUse"><polyline points="1,1 4,5 7,1" fill="none" stroke="#1e87c8" stroke-width="1.3"/></pattern>
      </defs>
      <rect x="0" y="0" width="798" height="8" fill="url(#chevH)"/>
      <rect x="0" y="200" width="798" height="8" fill="url(#chevH)"/>
      <rect x="0" y="8" width="8" height="192" fill="url(#chevV)"/>
      <rect x="790" y="8" width="8" height="192" fill="url(#chevV)"/>
    </svg>
    <h2 class="section-title">DURING THE LESSON</h2>
    <div class="abs col" style="left:37px">
      <h3>ON THE BOARD:</h3>
      <ul><li>Date</li><li>Learning intention</li><li>Success Criteria</li></ul>
    </div>
    <div class="abs col" style="left:251px">
      <h3 style="letter-spacing:-.3px">ACTIVE SUPERVISION – CHECK:</h3>
      <ul><li>All homework is complete</li><li>Bookwork meets expectations</li><li>All students are learning</li></ul>
    </div>
    <div class="abs col" style="left:520px;width:265px">
      <h3>UPHOLD POLICIES:</h3>
      <ul><li>Every child in uniform</li><li>No use of mobile phones and electronic devices</li><li>RollCall is marked in the first 15 minutes</li></ul>
    </div>
  </section>

  <section class="abs exit">
    <h2 class="section-title">EXIT</h2>
    <p class="exit-lead">EXIT STRATEGY USED TO CHECK FOR UNDERSTANDING<br>BEFORE YOU LEAVE...</p>
    <div class="abs check" style="left:2px">
      <svg width="34" height="30" viewBox="0 0 34 30" aria-hidden="true"><circle cx="14" cy="16" r="11" fill="none" stroke="#29abe2" stroke-width="2"/><polyline points="8,15 13,21 31,2" fill="none" stroke="#29abe2" stroke-width="3"/></svg>
      TECHNOLOGY IS CHECKED
    </div>
    <div class="abs check" style="left:281px">
      <svg width="34" height="30" viewBox="0 0 34 30" aria-hidden="true"><circle cx="14" cy="16" r="11" fill="none" stroke="#29abe2" stroke-width="2"/><polyline points="8,15 13,21 31,2" fill="none" stroke="#29abe2" stroke-width="3"/></svg>
      ENVIRONMENT LEFT NEAT AND TIDY
    </div>
    <div class="abs check" style="left:562px">
      <svg width="34" height="30" viewBox="0 0 34 30" aria-hidden="true"><circle cx="14" cy="16" r="11" fill="none" stroke="#29abe2" stroke-width="2"/><polyline points="8,15 13,21 31,2" fill="none" stroke="#29abe2" stroke-width="3"/></svg>
      DOORS AND WINDOWS LOCKED
    </div>
  </section>
  <svg class="abs exit-notch" width="48" height="14" viewBox="0 0 48 14" aria-hidden="true"><polygon points="0,0 48,0 24,14" fill="#0c4f8f"/></svg>

  <h2 class="abs recognise-title">RECOGNISE POSITIVE BEHAVIOUR BY</h2>
  <div class="abs reward" style="left:2px">
    <svg width="46" height="50" viewBox="0 0 46 50" aria-hidden="true"><polygon points="23,2 44,21 38,21 38,44 8,44 8,21 2,21" fill="#14174a"/><rect x="16" y="28" width="14" height="16" fill="#29abe2"/><polygon points="23,2 44,21 40,21 23,6 6,21 2,21" fill="#1e87c8"/></svg>
    Assigning house points
  </div>
  <div class="abs reward" style="left:281px">
    <svg width="46" height="50" viewBox="0 0 46 50" aria-hidden="true"><rect x="10" y="4" width="26" height="22" fill="#1e87c8"/><polygon points="3,22 43,22 43,46 3,46" fill="#14174a"/><polyline points="3,22 23,36 43,22" fill="none" stroke="#29abe2" stroke-width="2"/></svg>
    Postcard or Student of the Week
  </div>
  <div class="abs reward" style="left:562px">
    <svg width="46" height="50" viewBox="0 0 46 50" aria-hidden="true"><path d="M8 18 q-4 6 2 16 q8 12 18 14 q4 0 6-4 l-6-6 q-3 2-5 0 q-6-5-8-10 q0-2 2-4 l-4-8 q-3 0-5 2z" fill="#14174a"/><circle cx="32" cy="14" r="10" fill="none" stroke="#29abe2" stroke-width="2"/><polygon points="32,8 38,14 26,14" fill="#14174a"/><rect x="28" y="14" width="8" height="5" fill="#14174a"/></svg>
    Phone call home
  </div>

  <div class="abs ensure-band">ENSURE THAT YOU ALWAYS</div>

  <div class="abs habit" style="left:2px">
    <svg width="46" height="46" viewBox="0 0 46 46" aria-hidden="true"><circle cx="24" cy="26" r="16" fill="none" stroke="#1e87c8" stroke-width="3"/><rect x="20" y="4" width="8" height="4" fill="#14174a"/><line x1="24" y1="26" x2="30" y2="18" stroke="#14174a" stroke-width="2"/><rect x="2" y="6" width="16" height="11" rx="2" fill="#14174a"/></svg>
    Meet deadlines
  </div>
  <div class="abs habit" style="left:281px">
    <svg width="46" height="50" viewBox="0 0 46 50" aria-hidden="true"><rect x="14" y="2" width="28" height="18" rx="3" fill="none" stroke="#14174a" stroke-width="2"/><line x1="19" y1="9" x2="37" y2="9" stroke="#1e87c8" stroke-width="2"/><line x1="19" y1="14" x2="33" y2="14" stroke="#1e87c8" stroke-width="2"/><rect x="6" y="26" width="26" height="20" rx="4" fill="#1e87c8"/><polyline points="12,36 17,41 26,31" fill="none" stroke="#ffffff" stroke-width="2.5"/></svg>
    Following through on commitments
  </div>
  <div class="abs habit" style="left:562px">
    <svg width="90" height="44" viewBox="0 0 90 44" aria-hidden="true"><rect x="4" y="6" width="4" height="22" fill="#14174a"/><rect x="82" y="6" width="4" height="22" fill="#14174a"/><rect x="4" y="6" width="12" height="4" fill="#14174a"/><rect x="74" y="6" width="12" height="4" fill="#14174a"/><rect x="14" y="24" width="62" height="4" fill="#14174a"/><circle cx="33" cy="16" r="6" fill="#1e87c8"/><circle cx="57" cy="16" r="6" fill="#1e87c8"/></svg>
    Resolve all problems peacefully<br>without violence or abuse
  </div>
</main>
</body>
</html>
```